KAJU Freightways #ALLKAJU Business Cards & Letterhead

I am looking to business cards designed for our organization. We are currently undergoing a small re-branding that is taking place. Our organization is called KAJU Freightways and we are headquartered in Phoenix, AZ. We primarily provide transportation and logistics services to the Marlow Parcel Bureau who is our largest customer. I would like to see a design that incorporates name, title, contact info, website, and address (this will be different depending on the employee). I would also like to see some color on the business card using our logo colors or a variation. I would like our logo on the back of the business card with the website displayed. The final design should communicate that we are a next generation transportation operate that focuses on being driver-first, customer-centric, innovative, and sustainable.We would also like our #ALLKAJU catch phrase incorporated as well.

Target Market(s)

Transportation & Logistics

Industry/Entity Type

Trucking Company

Contact Information for Business Card

-First and Last Name
-Position Title
-Contact Phone
-Contact Email
-Physical Address

Font styles to use
Serif

Colors

Designer to choose colors to be used in the design.

Requirements
Must have
• -KAJU logo prominently displayed
• -#ALLKAJU catch phrase used
• -Some amount of color, design gradient, etc.
• -Logo on the back with website listed (https://www.kajufreightco.example)

```html
<!DOCTYPE html>
<html lang="en">
<head>
<meta charset="utf-8">
<title>KAJU Freightways Business Card</title>
<link rel="stylesheet" href="https://fonts.googleapis.com/css2?family=Lora:wght@400;500;700&display=swap">
<style>
  :root {
    --stage: #1b1b1c;
    --card: #232323;
    --card-edge: #2b2b2b;
    --accent: #6cc241;
    --ink: #ffffff;
    --ink-soft: #e6e6e6;
  }
  * { box-sizing: border-box; margin: 0; padding: 0; }
  html, body {
    width: 1200px; height: 900px; overflow: hidden;
    background: var(--stage);
    font-family: "Lora", serif;
    color: var(--ink);
  }
  .stage {
    position: relative; width: 1200px; height: 900px;
    display: flex; flex-direction: column; align-items: center; justify-content: center; gap: 40px;
  }
  .card {
    position: relative; width: 640px; height: 366px;
    background: linear-gradient(135deg, var(--card) 0%, var(--card-edge) 70%, #303030 100%);
    overflow: hidden;
    box-shadow: 0 18px 40px rgba(0,0,0,.55);
  }
  .card__band {
    position: absolute; left: 0; right: 0; bottom: 0; height: 6px;
    background: var(--accent);
  }
  .brand {
    position: absolute; display: flex; align-items: center; gap: 14px;
  }
  .brand__dot {
    flex: none; border-radius: 50%; background: var(--accent);
  }
  .brand__name {
    font-weight: 700; color: var(--ink); letter-spacing: 2px; line-height: 1;
  }
  /* back */
  .card--back .brand { left: 50%; top: 110px; transform: translateX(-50%); }
  .card--back .brand__dot { width: 20px; height: 20px; }
  .card--back .brand__name { font-size: 58px; }
  .tagline {
    position: absolute; left: 0; right: 0; top: 192px; text-align: center;
    font-size: 18px; font-weight: 500; letter-spacing: 4px; color: var(--accent);
  }
  .card--back .site {
    position: absolute; left: 0; right: 0; bottom: 44px; text-align: center;
    font-size: 17px; font-weight: 500; letter-spacing: 2.5px; color: var(--ink-soft);
  }
  /* front */
  .card--front .brand { left: 44px; top: 146px; }
  .card--front .brand__dot { width: 22px; height: 22px; }
  .card--front .brand__name { font-size: 62px; }
  .divider {
    position: absolute; left: 318px; top: 62px; width: 2px; height: 228px;
    background: var(--accent);
  }
  .contact { position: absolute; left: 350px; top: 64px; right: 14px; }
  .contact__name {
    font-size: 24px; font-weight: 500; color: var(--accent); letter-spacing: 1.5px;
    text-transform: uppercase; white-space: nowrap;
  }
  .contact__title { font-size: 17px; letter-spacing: 1px; color: var(--ink-soft); margin-top: 2px; }
  .contact__address { font-size: 17px; line-height: 1.3; letter-spacing: .5px; margin-top: 16px; color: var(--ink-soft); }
  .contact__list { list-style: none; margin-top: 12px; }
  .contact__item {
    display: flex; align-items: center; gap: 10px; white-space: nowrap;
    font-size: 16px; letter-spacing: .4px; line-height: 1.55; color: var(--ink-soft);
  }
  .contact__item svg { width: 13px; height: 13px; flex: none; }
  .contact__highlight { color: var(--accent); }
</style>
</head>
<body>
<main class="stage">
  <section class="card card--back" aria-label="Business card back">
    <div class="brand"><span class="brand__dot"></span><span class="brand__name">KAJU</span></div>
    <p class="tagline">#ALLKAJU</p>
    <p class="site">www.kajufreightco.example</p>
    <div class="card__band"></div>
  </section>

  <section class="card card--front" aria-label="Business card front">
    <div class="brand"><span class="brand__dot"></span><span class="brand__name">KAJU</span></div>
    <div class="divider"></div>
    <div class="contact">
      <h1 class="contact__name">Dana Whitfield</h1>
      <p class="contact__title">Director</p>
      <p class="contact__address">4170 North Cactus<br>Ridge Road<br>Phoenix, AZ 85029</p>
      <ul class="contact__list">
        <li class="contact__item">
          <svg viewBox="0 0 16 16" aria-hidden="true"><path d="M4 1l3 3-2 2c1 2 3 4 5 5l2-2 3 3-2 2C7 14 2 9 2 3z" fill="var(--accent)"/></svg>
          602-555-0148
        </li>
        <li class="contact__item">
          <svg viewBox="0 0 16 16" aria-hidden="true"><rect x="1.5" y="3.5" width="13" height="9" fill="none" stroke="var(--accent)" stroke-width="1.5"/><path d="M1.5 3.5l6.5 5 6.5-5" fill="none" stroke="var(--accent)" stroke-width="1.5"/></svg>
          info@kajufreightco.example
        </li>
        <li class="contact__item">
          <svg viewBox="0 0 16 16" aria-hidden="true"><circle cx="8" cy="8" r="6.5" fill="none" stroke="var(--accent)" stroke-width="1.5"/><path d="M1.5 8h13M8 1.5c-3 3.5-3 9.5 0 13M8 1.5c3 3.5 3 9.5 0 13" fill="none" stroke="var(--accent)" stroke-width="1.2"/></svg>
          <span>www.<span class="contact__highlight">kajufreightco</span>.example</span>
        </li>
      </ul>
    </div>
    <div class="card__band"></div>
  </section>
</main>
</body>
</html>
```